Web design for sitter site

We will be launching a sitter site in the coming months that focuses on sitters for children. The name of this site will be NestWatch.com
We will need:
1. main page design
2. site logo designed
3. subpages as well for the look of people's profiles, and job listings, etc (see links below)
We only need the design, photos, font files, etc. We do not need this site coded (no html), a ps job is fine.
Some competing sites in the space include - tendlane.com and brio.com
http://www.pebble-keeper.example/images/profile1.jpg
http://marrowbooks.example/wp-content/uploads/2013/09/brio-review.png
http://www.quillmont.example/hr/photos/tend_lane2.jpg
Thanks for your interest!
Mothers of children, mainly women
Online

```html
<!DOCTYPE html>
<html lang="en">
<head>
<meta charset="utf-8">
<title>Hushnook – Home</title>
<link href="https://fonts.googleapis.com/css2?family=Open+Sans:wght@400;600;700&display=swap" rel="stylesheet">
<style>
:root{
  --blue-deep:#0f4a8c;
  --blue:#1b62ad;
  --blue-nav:#1a5a9e;
  --orange:#f28705;
  --orange-dark:#c94e00;
  --orange-hi:#ff8a1c;
  --cyan:#1fa3d8;
  --text:#333;
  --muted:#555;
  --footer:#2b2b2b;
  --footer-base:#1f1f1f;
  --white:#fff;
}
*{margin:0;padding:0;box-sizing:border-box}
html,body{width:690px;height:1200px;overflow:hidden}
body{font-family:"Open Sans",Arial,sans-serif;color:var(--text);background:var(--white);position:relative}
h1,h2,h3,h4{font-weight:400}
.abs{position:absolute}

/* header */
.site-header{left:0;top:0;width:690px;height:76px;background:linear-gradient(#0d427f,var(--blue-deep))}
.brand{left:104px;top:31px;color:var(--white);font-weight:700;font-size:15px;letter-spacing:.5px}
.search{left:428px;top:26px;width:132px;height:24px;background:#eef5fb;font-size:6px;color:#9aa;padding:0 8px;line-height:24px}
.search-btn{left:560px;top:26px;width:26px;height:24px;background:var(--orange-hi);display:flex;align-items:center;justify-content:center}

/* nav */
.main-nav{left:0;top:76px;width:690px;height:30px;background:linear-gradient(var(--orange-hi),#e85a00)}
.nav-list{left:104px;top:76px;height:30px;display:flex;list-style:none;font-size:6.6px;color:var(--white)}
.nav-list li{padding:0 8px;line-height:30px}
.nav-list li.active{background:var(--orange-dark);padding:0 8.5px}
.account{left:497px;top:76px;width:89px;height:30px;background:var(--blue-nav);display:flex;font-size:6.6px;color:var(--white)}
.account span{flex:1;text-align:center;line-height:30px}
.account span+span{border-left:1px solid #3f7cbd}

/* hero */
.hero{left:0;top:106px;width:690px;height:316px;background:radial-gradient(circle at 50% 40%,#2a7ac7,#1559a3 70%)}
.slider{left:102px;top:120px;width:484px;height:258px;background:var(--white);padding:4px;box-shadow:0 14px 18px rgba(0,0,0,.25)}
.slide-photo{width:100%;height:100%;background:linear-gradient(90deg,#6a9a2e,#b7d34a 45%,#8cbd3c)}
.caption{left:114px;top:281px;width:248px;height:53px;background:rgba(40,40,40,.6);color:var(--white);font-size:11.5px;line-height:20px;padding:6px 13px}
.dots{left:327px;top:355px;display:flex;gap:3px}
.dots i{width:7px;height:7px;border-radius:50%;background:#3b6ea5;display:block}
.dots i.on{background:#1e4f86}

/* welcome */
.welcome-title{left:104px;top:444px;font-size:12px;color:#222;font-weight:400}
.welcome-text{left:104px;top:468px;width:310px;font-size:6.3px;line-height:12px;color:var(--text)}
.read-more{left:104px;top:525px;font-size:6px;color:var(--cyan);text-decoration:underline}
.video-thumb{left:426px;top:441px;width:160px;height:95px;background:linear-gradient(135deg,#d9b47a,#b98a52 60%,#9c6c3c);border:1px solid #ccc}
.play{left:491px;top:473px;width:28px;height:28px;border-radius:50%;background:rgba(220,40,40,.85)}

/* what we do */
.wwd-bar{left:104px;top:558px;width:482px;height:28px;background:var(--orange);color:var(--white);font-weight:700;font-size:12px;line-height:28px;padding-left:11px}
.tab{left:104px;width:106px;background:var(--orange);color:var(--white);font-weight:700;font-size:8px;padding-left:27px;display:flex;align-items:center}
.tab.current{background:var(--white);color:var(--orange);line-height:12px}
.wwd-base{left:104px;top:771px;width:482px;height:5px;background:var(--orange)}
.care-photo{top:629px;width:114px;height:74px;background:linear-gradient(135deg,#e9e4dc,#c9bca9 50%,#7fa1c0)}
.care-caption{top:706px;width:100px;font-size:6px;line-height:12px;color:var(--text)}

/* how it works / news */
.section-title{font-size:8.5px;color:#222;font-weight:400}
.step-icon{width:32px;height:32px;border-radius:50%;background:var(--cyan);display:flex;align-items:center;justify-content:center}
.step-title{left:144px;font-size:8px;color:var(--cyan);letter-spacing:.1px}
.step-text{left:149px;width:170px;font-size:6px;line-height:12px;color:var(--muted)}
.divider{left:334px;top:824px;width:1px;height:168px;background:#ccc}
.news-thumb{left:350px;width:74px;height:52px;background:linear-gradient(135deg,#a8c27a,#cfd8b4 50%,#6e8f4a);border:1px solid #ddd}
.news-date{left:350px;width:40px;height:9px;background:var(--blue-nav);color:var(--white);font-size:5px;line-height:9px;padding-left:3px}
.news-title{left:431px;font-size:8px;color:#333;font-weight:400}
.news-text{left:431px;width:155px;font-size:6px;line-height:12px;color:var(--muted)}
.news-text a{color:var(--cyan);text-decoration:none}
.view-all{left:536px;top:979px;width:50px;height:20px;background:var(--orange-hi);color:var(--white);font-size:6px;line-height:20px;text-align:center;border-bottom:2px solid #d85400}

/* footer */
.site-footer{left:0;top:1020px;width:690px;height:128px;background:var(--footer)}
.foot-title{top:1040px;font-size:8px;font-weight:700;color:var(--cyan);letter-spacing:.2px}
.foot-links{top:1060px;list-style:none;font-size:6px;line-height:13.6px;color:#ddd}
.foot-links li::before{content:"→ ";font-size:5px;color:#ccc}
.foot-links li.hover{color:var(--orange)}
.map{left:432px;top:1057px;width:146px;height:73px;background:linear-gradient(135deg,#e6e2d8,#f0ecdf 50%,#e4dccb);border:2px solid #ddd}
.footer-base{left:0;top:1148px;width:690px;height:52px;background:var(--footer-base)}
.legal{left:104px;top:1157px;font-size:7px;color:#ddd}
.copyright{left:104px;top:1180px;font-size:5px;color:#bbb}
.social{top:1160px;width:26px;height:26px;border-radius:50%;border:2px solid #fff}
</style>
</head>
<body>

<header class="abs site-header"></header>
<div class="abs brand">HUSHNOOK</div>
<div class="abs search">Search....</div>
<div class="abs search-btn">
  <svg width="11" height="11" viewBox="0 0 12 12"><circle cx="5" cy="5" r="3.5" fill="none" stroke="#fff" stroke-width="1.6"/><line x1="7.6" y1="7.6" x2="11" y2="11" stroke="#fff" stroke-width="1.8"/></svg>
</div>

<nav class="abs main-nav"></nav>
<ul class="abs nav-list">
  <li class="active">Home</li><li>What We Offer</li><li>Care Services</li><li>House keeping</li><li>How It Works</li><li>Contact Us</li><li>Blog</li>
</ul>
<div class="abs account"><span>Join Now</span><span>Login</span></div>

<section class="abs hero"></section>
<div class="abs slider"><div class="slide-photo" role="img" aria-label="Photo of a smiling caregiver doing crafts with young children at a table"></div></div>
<div class="abs caption">Lorem ipsum dolor sit amet consectetur adipisicing elit sed.</div>
<div class="abs dots"><i class="on"></i><i></i><i></i><i></i></div>

<h1 class="abs welcome-title">WELCOME TO OUR HUSHNOOK</h1>
<p class="abs welcome-text">Lorem ipsum dolor sit amet, consectetur adipisicing elit, sed do eiusmod Incididunt ut labore et dolore magna aliqua. Ut enim ad minim veniam, quis nostrud exercitation ullamco. laboris nisi ut aliquip ex ea commodo consequat. Duis aute irure dolor in reprehenderit in voluptate velit esse cillum dolore eu fugiat nulla pariatur.</p>
<a class="abs read-more">READ MORE</a>
<div class="abs video-thumb" role="img" aria-label="Video still of two young girls playing with toys in a playroom"></div>
<div class="abs play"><svg width="28" height="28" viewBox="0 0 28 28"><path d="M11 8 L20 14 L11 20Z" fill="#fff"/></svg></div>

<h2 class="abs wwd-bar">What We Do</h2>
<div class="abs tab" style="top:586px;height:44px">Child Care</div>
<div class="abs tab current" style="top:630px;height:49px">Adult and<br>Senior Care</div>
<div class="abs tab" style="top:679px;height:44px;border-top:1px solid #fff">Pet Care</div>
<div class="abs tab" style="top:723px;height:48px;border-top:1px solid #fff">Home Care</div>
<div class="abs wwd-base"></div>
<svg class="abs" style="left:564px;top:599px" width="26" height="16" viewBox="0 0 26 16">
  <circle cx="5" cy="6" r="4.5" fill="#f28705"/><path d="M6.5 3.5 L3.5 6 L6.5 8.5Z" fill="#fff"/>
  <circle cx="17" cy="6" r="4.5" fill="#1fa3d8"/><path d="M15.5 3.5 L18.5 6 L15.5 8.5Z" fill="#fff"/>
</svg>
<div class="abs care-photo" style="left:218px" role="img" aria-label="Photo of a caregiver hugging an elderly woman"></div>
<div class="abs care-photo" style="left:344px;background:linear-gradient(135deg,#7a9a4e,#c9c2a8 50%,#8aa86a)" role="img" aria-label="Photo of two seniors sitting outdoors"></div>
<div class="abs care-photo" style="left:472px" role="img" aria-label="Photo of a caregiver with an elderly woman"></div>
<p class="abs care-caption" style="left:221px">Lorem ipsum dolor sit amet adipisicing elit sed.</p>
<p class="abs care-caption" style="left:350px">Lorem ipsum dolor sit amet adipisicing elit sed.</p>
<p class="abs care-caption" style="left:476px">Lorem ipsum dolor sit amet adipisicing elit sed.</p>

<h3 class="abs section-title" style="left:105px;top:794px">How it works?</h3>
<div class="abs step-icon" style="left:105px;top:826px">
  <svg width="18" height="14" viewBox="0 0 18 14"><circle cx="9" cy="4" r="2.6" fill="#fff"/><path d="M4 13 Q9 5 14 13Z" fill="#fff"/><circle cx="4" cy="5" r="1.8" fill="#fff"/><circle cx="14" cy="5" r="1.8" fill="#fff"/><path d="M0.5 12 Q4 6 6.5 10Z M17.5 12 Q14 6 11.5 10Z" fill="#fff"/></svg>
</div>
<div class="abs step-title" style="top:836px">VESTIBULINIA EST PROIN DICTUM</div>
<p class="abs step-text" style="top:857px">Vestibulum ilis lacinia est. Proin dictum elem velit. Fus ce euismod consequat anteum dolor sit amet, con-sectetuer adipisci.</p>
<div class="abs step-icon" style="left:105px;top:908px">
  <svg width="16" height="16" viewBox="0 0 16 16"><path d="M2 7 H5 V14 H2Z M6 7 L9 2 Q11 2 10.5 5 L10 6.5 H14 Q15 7 14.5 8.5 L13 13.5 Q12.5 14 11.5 14 H6Z" fill="none" stroke="#fff" stroke-width="1.4" stroke-linejoin="round"/></svg>
</div>
<div class="abs step-title" style="top:918px">VESTIBULINIA EST PROIN DICTUM</div>
<p class="abs step-text" style="top:936px">Vestibulum ilis lacinia est. Proin dictum elem velit. Fusce euismod consequat anteum dolor sit amet, consectetuer adipisci.</p>

<div class="abs divider"></div>

<h3 class="abs section-title" style="left:349px;top:796px">News &amp; Events</h3>
<div class="abs news-thumb" style="top:830px" role="img" aria-label="Photo of a child lying in grass with a dog"></div>
<div class="abs news-date" style="top:871px">Mar 24, 2014</div>
<h3 class="abs news-title" style="top:826px">Praesent justo dolor</h3>
<p class="abs news-text" style="top:850px">Vestibulum ilis lacinia est. Proin dictum elem velit. Fusce euismod consequat anteum dolor sit amet, consectetuer adipisci.... <a>READ MORE</a></p>
<div class="abs news-thumb" style="top:904px;background:linear-gradient(135deg,#d98aa8,#f1d6c8 50%,#9bb8d8)" role="img" aria-label="Photo of a young girl drawing at a table"></div>
<div class="abs news-date" style="top:945px">Mar 24, 2014</div>
<h3 class="abs news-title" style="top:900px">Praesent justo dolor</h3>
<p class="abs news-text" style="top:924px">Vestibulum ilis lacinia est. Proin dictum elem velit. Fusce euismod consequat anteum dolor sit amet, consectetuer adipisci.... <a>READ MORE</a></p>
<div class="abs view-all">VIEW ALL</div>

<footer class="abs site-footer"></footer>
<h4 class="abs foot-title" style="left:106px">COMPANY</h4>
<ul class="abs foot-links" style="left:123px">
  <li>About Us</li><li>Investor Relations</li><li>Mara's Blog</li><li>Help</li><li>Safety Center</li><li>Careers</li>
</ul>
<h4 class="abs foot-title" style="left:263px">POPULAR TOPICS</h4>
<ul class="abs foot-links" style="left:281px">
  <li>Babysitters</li><li class="hover">Nannies</li><li>Child</li><li>Housekeepers</li><li>Tutors</li>
</ul>
<h4 class="abs foot-title" style="left:426px">OUR LOCATION</h4>
<div class="abs map" role="img" aria-label="Street map showing the office location"></div>

<div class="abs footer-base"></div>
<div class="abs legal">Privacy Policy | Terms &amp; Conditions | Contact us | Sitemap</div>
<div class="abs copyright">copyright@ 2014 .all right reserved.</div>
<div class="abs social" style="left:443px;background:#2d5ea8"></div>
<div class="abs social" style="left:473px;background:#1ca0dc"></div>
<div class="abs social" style="left:502px;background:#c8202a"></div>
<div class="abs social" style="left:532px;background:#d94b36"></div>
<div class="abs social" style="left:561px;background:#f26522"></div>

</body>
</html>
```